Interior Plaster, Plasterboard Fixing & Installation Business CardDesign

BRANVO The name was formed by me, in talking to my accountant, whilst skim coating his walls and I had seen an imperfection in a wall that needed to be skim coated to deflect the light from the imperfection. I responded to him saying...."just Bran Vo". The idea originates from the process of applying a skim coat of interior plaster to a wall to achieve a smoother surface. This is required prior to many applications, applying wall paper, preparation for paint, after removing wall paper, improving aesthetics, joints that have not been properly jointed etc. Different types of light reflected on the surface, makes poor jointing more visible. In addition, the businesses key functions will be interior plastering, plaster board installation (ceilings and walls) and plasterboard jointing to a level that is prepared for a painter. Once the plaster is applied the surface requires sanding using different types of sanding equipment manual and electronic, including the use of specialised paint-on sealers for the surface. I believe the name is simple, easy to remember, but may be read incorrectly. I have had people ask if it was Bran Vo, referring to information technology.

For now, this entire concept is driven by passion and started 2 years ago whilst renovating my own home.

I need to be able to use your expertise to translate my ideas, starting with business card and progressing to a website incorporating anything and everything in between. The final design should be easy to understand, read and standout with an element of uniqueness. Humour maybe an option, or the idea of leaving a prospect with something that is thought provoking.
Updates

Hi All Ideas look fine so far, but would expect to see different colour options. I am thinking plaster thats cream in colour, so more earthy colour on the card. A picture of a trowel to replace the I in BRANVO maybe. I like the swirl that is created by a notched trowel moving through plaster. Perhaps a more modern or fresher look. With BRANVO, could you consider reversing the direction of the K for instance facing in the opposite direction. In saying this I look to you for your experience and expertise with the idea. The other option with the K, could be to remove the first straight line, i hope that my explanation helps. Sorry if it doesn't. Thanks heaps :)

Please include the type of service. Plasterboard Services

I have considered the idea of the K being reversed, and I am of the view that it presents a challenge reading and understanding. Moving forward I would however like to use the K in the normal direction but without the first straight line. I need to see more colour options that are grey or earthy. Can a picture of a trowel be included if it makes sense and with that tool being frequently used in plastering.

Industry/Entity Type

Business

Contact Information for Business Card

Company name: BranVo
Name: Dorian Pekke
Title: Director
Email address: pekkedp@mailvora.example
Mobile number: 0210 481 7092
Address: 17 Tamsin Lane, Glenfield, Auckland, 0629

```html
<!DOCTYPE html>
<html lang="en">
<head>
<meta charset="utf-8">
<title>BranVo Business Card</title>
<link href="https://fonts.googleapis.com/css2?family=Exo+2:wght@400;800&display=swap" rel="stylesheet">
<style>
  :root {
    --backdrop: #9c9c9c;
    --card: #f3f3f1;
    --brand-orange: #f0631f;
    --ink: #2b2b2b;
    --ink-soft: #3a3a3a;
    --bar-dark: #2e2a2b;
  }
  * { margin: 0; padding: 0; box-sizing: border-box; }
  html, body { width: 1200px; height: 894px; overflow: hidden; }
  body {
    background: var(--backdrop);
    font-family: "Exo 2", "Helvetica Neue", Arial, sans-serif;
    color: var(--ink);
    position: relative;
  }
  .card {
    position: absolute;
    left: 260px;
    width: 680px;
    height: 388px;
    background: var(--card);
    box-shadow: 0 6px 18px rgba(0,0,0,0.25);
  }
  .card--front { top: 30px; }
  .card--back { top: 476px; }

  .brand-name {
    font-weight: 800;
    color: var(--brand-orange);
    letter-spacing: 0.5px;
    line-height: 1;
  }
  .card--front .brand-name {
    position: absolute;
    left: 0; right: 0; top: 140px;
    text-align: center;
    font-size: 92px;
  }
  .service-line {
    position: absolute;
    left: 0; right: 0; top: 248px;
    text-align: center;
    font-size: 15px;
    letter-spacing: 3px;
    text-transform: uppercase;
    color: var(--ink-soft);
  }

  .card--back .brand-name {
    position: absolute;
    left: 150px; top: 78px;
    font-size: 58px;
  }
  .person {
    position: absolute;
    left: 152px; top: 146px;
    text-transform: uppercase;
  }
  .person__name { font-size: 21px; font-weight: 400; letter-spacing: 1px; }
  .person__title { font-size: 13px; letter-spacing: 1.4px; color: var(--ink-soft); margin-top: 2px; }

  .contact {
    position: absolute;
    list-style: none;
    font-size: 14px;
    letter-spacing: 0.6px;
    line-height: 1.25;
  }
  .contact li { display: flex; align-items: flex-start; gap: 8px; margin-bottom: 6px; }
  .contact svg { flex: none; width: 13px; height: 13px; margin-top: 2px; }
  .contact--location { left: 60px; top: 212px; }
  .contact--reach { left: 392px; top: 226px; }

  .rule {
    position: absolute;
    top: 304px;
    height: 10px;
  }
  .rule--orange { left: 0; width: 360px; background: var(--brand-orange); }
  .rule--dark { left: 360px; width: 250px; background: var(--bar-dark); }
</style>
</head>
<body>

<section class="card card--front" aria-label="Card front">
  <div class="brand-name">BranVo</div>
  <div class="service-line">Plasterboard Services</div>
</section>

<section class="card card--back" aria-label="Card back">
  <div class="brand-name">BranVo</div>
  <div class="person">
    <div class="person__name">Dorian Pekke</div>
    <div class="person__title">Director</div>
  </div>

  <ul class="contact contact--location">
    <li>
      <svg viewBox="0 0 12 12" aria-hidden="true"><path d="M6 0.5a4 4 0 0 0-4 4c0 3 4 7 4 7s4-4 4-7a4 4 0 0 0-4-4zm0 5.6a1.6 1.6 0 1 1 0-3.2 1.6 1.6 0 0 1 0 3.2z" fill="var(--ink)"/></svg>
      <span>17 Tamsin Lane, Glenfield<br>Auckland, 0629</span>
    </li>
    <li>
      <svg viewBox="0 0 12 12" aria-hidden="true"><circle cx="6" cy="6" r="5" fill="none" stroke="var(--ink)" stroke-width="1.2"/><ellipse cx="6" cy="6" rx="2.2" ry="5" fill="none" stroke="var(--ink)" stroke-width="1"/><line x1="1" y1="6" x2="11" y2="6" stroke="var(--ink)" stroke-width="1"/></svg>
      <span>www.branvo.example</span>
    </li>
  </ul>

  <ul class="contact contact--reach">
    <li>
      <svg viewBox="0 0 12 12" aria-hidden="true"><path d="M2.5 1h2l1 2.8-1.3 1a6.5 6.5 0 0 0 3 3l1-1.3L11 7.5v2A1.5 1.5 0 0 1 9.5 11 8.5 8.5 0 0 1 1 2.5 1.5 1.5 0 0 1 2.5 1z" fill="var(--ink)"/></svg>
      <span>0210 481 7092</span>
    </li>
    <li>
      <svg viewBox="0 0 12 12" aria-hidden="true"><rect x="3" y="0.5" width="6" height="11" rx="1" fill="none" stroke="var(--ink)" stroke-width="1.2"/><line x1="5" y1="9.6" x2="7" y2="9.6" stroke="var(--ink)" stroke-width="1"/></svg>
      <span>0210 481 7092</span>
    </li>
    <li>
      <svg viewBox="0 0 12 12" aria-hidden="true"><rect x="0.6" y="2" width="10.8" height="8" fill="none" stroke="var(--ink)" stroke-width="1.2"/><path d="M0.8 2.3 6 6.6l5.2-4.3" fill="none" stroke="var(--ink)" stroke-width="1.1"/></svg>
      <span>pekkedp@mailvora.example</span>
    </li>
  </ul>

  <div class="rule rule--orange"></div>
  <div class="rule rule--dark"></div>
</section>

</body>
</html>
```